Hollow Thicket, a 3d voxel survival video game needs a card for gaming conventions

I am the lead developer for Hollow Thicket http://www.HollowThicket.example and need a business card to hand out at an indie gaming convention
The card would need to include the game name, website url, my name, position (Lead Developer), e-mail and phone number
The game is a 3d, voxel (with smooth terrain) based survival game with guns and wildlife. The main icon of the game would likely be a grizzly bear but I am willing to accept other designs too.
Attached is a media kit for the game with some images you can use but don't have to its just what little art I can provide. Anything on the website or from the video game can also be used. unrelated art can also be used.
Target Market(s)
Indie Developers/publishers at conferences
Industry/Entity Type
Games
Contact Information for Business Card
Name: Corin Waldrick
Position: Lead Developer
E-mail: Pale_Kettle@mailbox.example
Phone number: 555-372-1186

```html
<!DOCTYPE html>
<html lang="en">
<head>
<meta charset="utf-8">
<title>Hollow Thicket – Business Card</title>
<link href="https://fonts.googleapis.com/css2?family=Roboto:wght@400&family=Saira+Semi+Condensed:wght@600&display=swap" rel="stylesheet">
<style>
  :root {
    --backdrop: #a8a6a7;
    --olive-light: #d8d3b8;
    --olive-mid: #8e8a68;
    --olive-dark: #3c3a22;
    --charcoal: #1f2022;
    --charcoal-edge: #2a2b2e;
    --bear-brown: #7a5535;
    --bear-shadow: #3e2a1a;
    --logo-red: #a8342a;
    --khaki: #8a8a6c;
    --accent-red: #9c1a18;
    --text-light: #f2f2f2;
    --rule: #c9c9c9;
  }
  * { margin: 0; padding: 0; box-sizing: border-box; }
  html, body { width: 1200px; height: 1200px; overflow: hidden; }
  body {
    background: var(--backdrop);
    position: relative;
    font-family: "Roboto", Arial, sans-serif;
  }
  .card { position: absolute; width: 714px; overflow: hidden; }

  /* Front */
  .card-front {
    left: 237px; top: 118px; height: 420px;
    background: radial-gradient(ellipse 60% 62% at 52% 56%, var(--olive-light) 0%, #b3ad8d 40%, var(--olive-mid) 70%, var(--olive-dark) 100%);
  }
  .front-bear {
    position: absolute; left: 233px; top: 47px; width: 175px; height: 180px;
    background: radial-gradient(ellipse 60% 60% at 55% 45%, var(--bear-brown) 0%, var(--bear-shadow) 70%, rgba(62,42,26,0) 100%);
  }
  .front-logo {
    position: absolute; left: 0; right: 0; top: 232px;
    text-align: center;
    font-family: "Saira Semi Condensed", "Arial Narrow", sans-serif;
    font-weight: 600; font-size: 56px; letter-spacing: 2px;
    color: var(--logo-red); text-transform: uppercase;
  }

  /* Back */
  .card-back {
    left: 229px; top: 643px; height: 422px;
    background: linear-gradient(160deg, var(--charcoal-edge), var(--charcoal));
  }
  .back-bear {
    position: absolute; left: 3px; top: 37px; width: 178px; height: 220px;
    background: radial-gradient(ellipse 55% 55% at 50% 45%, #9a6e48 0%, var(--bear-brown) 45%, rgba(60,45,35,0) 100%);
  }
  .back-logo {
    position: absolute; right: 50px; top: 46px;
    font-family: "Saira Semi Condensed", "Arial Narrow", sans-serif;
    font-weight: 600; font-size: 40px; letter-spacing: 2px;
    color: var(--logo-red); text-transform: uppercase;
  }
  .holder { position: absolute; right: 40px; top: 210px; text-align: right; color: var(--text-light); }
  .holder-name {
    font-family: "Saira Semi Condensed", "Arial Narrow", sans-serif;
    font-weight: 600; font-size: 29px; line-height: 1.1;
  }
  .holder-role { font-size: 17px; margin-top: 4px; }
  .divider { position: absolute; left: 36px; top: 263px; width: 486px; height: 1px; background: var(--rule); }
  .contacts { position: absolute; left: 34px; top: 292px; list-style: none; color: var(--text-light); font-size: 18px; }
  .contacts li { display: flex; align-items: center; height: 25.5px; }
  .contacts svg { width: 18px; height: 16px; margin-right: 19px; fill: var(--text-light); }
  .footer-band { position: absolute; left: 0; bottom: 0; width: 400px; height: 20px; background: var(--khaki); }
  .footer-accent { position: absolute; left: 0; bottom: 0; width: 714px; height: 42px; }
</style>
</head>
<body>

  <section class="card card-front">
    <div class="front-bear" role="img" aria-label="Photo of a roaring grizzly bear"></div>
    <div class="front-logo">Hollow Thicket</div>
  </section>

  <section class="card card-back">
    <div class="back-bear" role="img" aria-label="Photo of a grizzly bear standing on a rock"></div>
    <div class="back-logo">Hollow Thicket</div>

    <div class="holder">
      <div class="holder-name">Corin Waldrick</div>
      <div class="holder-role">Lead Developer</div>
    </div>
    <div class="divider"></div>

    <ul class="contacts">
      <li>
        <svg viewBox="0 0 18 16" aria-hidden="true"><path d="M1 5c0-2 3-3 8-3s8 1 8 3v1h-4V4.5H5V6H1zM4 7h10l2 8H2zM9 9a2.2 2.2 0 1 0 0 4.4A2.2 2.2 0 0 0 9 9z"/></svg>
        555-372-1186
      </li>
      <li>
        <svg viewBox="0 0 18 16" aria-hidden="true"><circle cx="9" cy="8" r="7" fill="none" stroke="#f2f2f2" stroke-width="1.4"/><ellipse cx="9" cy="8" rx="3" ry="7" fill="none" stroke="#f2f2f2" stroke-width="1.2"/><path d="M2 8h14M3 4.5h12M3 11.5h12" stroke="#f2f2f2" stroke-width="1.1"/></svg>
        www.hollowthicket.example
      </li>
      <li>
        <svg viewBox="0 0 18 16" aria-hidden="true"><path d="M1 3h16v10H1z"/><path d="M1 3l8 6 8-6M1 13l6-5M17 13l-6-5" fill="none" stroke="#1f2022" stroke-width="1.3"/></svg>
        Pale_Kettle@mailbox.example
      </li>
    </ul>

    <div class="footer-band"></div>
    <svg class="footer-accent" viewBox="0 0 714 42" aria-hidden="true">
      <polygon points="376,42 401,0 714,0 714,42" fill="var(--accent-red)"/>
    </svg>
  </section>

</body>
</html>
```